BRN website video quote promotion tiles

We are promoting vehicle leasing by video, which contains several quotation examples imported from the video. We must re-vamp the quotation tiles, contact boxes, and contact form. The first tile is generated from the video, so this must be a separate project. We are looking for a welcoming, professional flow and leave color choices to design with an emphasis on communication prompts, and additional prompts in the design would be welcome.

Target Market(s)

Any Customer interaction from the tile quotes, contact, call, message,

Industry/Entity Type

vehicle leasing

Coding

Coded - Design and coding required

Number of Pages Required

1 page

Colors

Designer to choose colors to be used in the design.

Requirements
Must have
• emphasis on point of contact and visual impact on quote tile excluding main one
Should not have
• changes to the quote structure as these imported from video pricing no changes to main image as this template which can addressed as separate project

```html
<!DOCTYPE html>
<html lang="en">
<head>
<meta charset="utf-8">
<title>Contract Hire Quote Tiles</title>
<link href="https://fonts.googleapis.com/css2?family=Roboto:wght@400;500;700&family=Roboto+Condensed:wght@700&family=Poppins:wght@400;600;700&family=Passion+One&display=swap" rel="stylesheet">
<style>
:root{
  --stage:#9a9a9a;
  --board:#e5e1e1;
  --navy:#1b2f6e;
  --teal:#13bfc3;
  --gold:#f0c23c;
  --gold-soft:#f6dc86;
  --orange:#f08a0c;
  --orange-deep:#e0823a;
  --green:#1aa31f;
  --ink:#333;
  --ink-soft:#444;
  --white:#fff;
  --field-line:#b9bfcc;
}
*{box-sizing:border-box;margin:0;padding:0}
html,body{width:1200px;height:675px;overflow:hidden}
body{background:radial-gradient(ellipse at 40% 45%,#6a6a6a 0%,var(--stage) 70%);font-family:"Roboto",sans-serif;position:relative}

.tile-board{position:absolute;left:87px;top:79px;width:330px;height:518px;background:var(--board);box-shadow:0 10px 40px rgba(0,0,0,.35)}
.quote-tile{position:absolute;left:35px;width:260px;height:139px;border-radius:10px;background:var(--white);overflow:hidden}
.quote-tile svg.tile-shape{position:absolute;inset:0}
.tile-teal{top:31px;border:2px solid #bfc3c8}
.tile-gold{top:189px;border:2px solid var(--gold)}
.tile-navy{top:346px;border:2px solid #c9ccd2;background:linear-gradient(170deg,#fff 40%,#eef0f4 100%)}

.price{position:absolute;right:9px;top:9px;text-align:right;color:var(--white);font-family:"Roboto",sans-serif;font-weight:700;font-size:12px;line-height:1}
.price small{display:block;font-size:6.5px;margin-top:6px;font-weight:700}
.price .amount-accent{color:var(--orange)}

.title-pill{position:absolute;left:9px;top:9px;width:116px;height:28px;border-radius:14px;display:flex;align-items:center;justify-content:center;color:var(--white);font-size:11px;font-weight:500;letter-spacing:.2px}
.pill-navy{background:var(--navy)}
.pill-gold{background:#e9bf3e;font-family:"Poppins",sans-serif;font-weight:700;font-size:11px}

.terms{position:absolute;left:26px;font-size:11px;font-weight:500;color:var(--ink)}
.includes{position:absolute;left:26px;font-size:8.5px;color:var(--ink-soft)}
.tile-gold .terms,.tile-gold .includes{font-family:"Poppins",sans-serif;left:23px}
.tile-gold .terms{font-weight:600}

.headline{position:absolute;left:23px;top:16px;font-family:"Passion One",sans-serif;font-size:19px;font-weight:400;letter-spacing:.3px}
.headline .word-a{color:var(--orange-deep)}
.headline .word-b{color:var(--navy)}
.divider{position:absolute;left:9px;right:9px;top:91px;height:1px;background:#d6d6d6}

.icon-row{position:absolute;left:26px;top:51px;display:flex;align-items:center;gap:4px;font-size:11px;font-weight:500;color:var(--ink)}
.icon-row svg{width:10px;height:10px}
.icon-row .gap{margin-left:4px}

.contact-btn{position:absolute;height:25px;width:83px;border-radius:13px;display:flex;align-items:center;gap:5px;padding-left:5px;color:var(--white);font-size:8px;font-weight:700;letter-spacing:.2px}
.contact-btn .btn-icon{width:16px;height:16px;border-radius:50%;background:var(--white);display:flex;align-items:center;justify-content:center}
.btn-orange{background:var(--orange)}
.btn-muted{background:var(--orange-deep)}
.btn-gradient{background:linear-gradient(180deg,#ffa21a,#ea6a0a)}
.btn-gradient .btn-icon{background:transparent}

.chat-badge{position:absolute;width:24px;height:24px;border-radius:50%;background:var(--green);color:var(--white);display:flex;align-items:center;justify-content:center;font-size:6px;font-weight:700}

.form-panel{position:absolute;left:443px;top:79px;width:670px;height:321px;overflow:hidden;box-shadow:0 10px 40px rgba(0,0,0,.35)}
.hero-photo{position:absolute;inset:0;background:linear-gradient(160deg,#dfe9f4 0%,#c8d6e8 35%,#4f6fb0 65%,#18357f 100%)}
.contact-form{position:absolute;left:49px;top:44px;width:312px;height:231px;border:3px solid #9aa9cc;border-radius:10px;background:rgba(255,255,255,.93)}
.form-title{position:absolute;left:30px;top:17px;font-family:"Roboto Condensed",sans-serif;font-weight:700;font-size:15.5px;color:#111}
.field{position:absolute;height:28px;border:1px solid var(--field-line);border-radius:3px;background:#fff;display:flex;align-items:flex-start;padding:4px 0 0 3px;gap:4px;font-size:8px;color:#222}
.field .field-icon{width:19px;height:19px;border-radius:50%;border:1px solid #d3d6dd;display:flex;align-items:center;justify-content:center;flex:none}
.field span{line-height:19px}
.field-name{left:30px;top:53px;width:120px}
.field-email{left:156px;top:53px;width:120px}
.field-phone{left:30px;top:89px;width:246px}
.field-message{left:30px;top:125px;width:246px;height:51px}
.submit-btn{position:absolute;left:31px;top:180px;width:78px;height:30px;border-radius:15px;background:linear-gradient(180deg,#f3942f,#d9560e);color:#fff;font-weight:700;font-size:9px;display:flex;align-items:center;justify-content:center}
.close-btn{position:absolute;right:-4px;top:-4px;width:30px;height:30px;border-radius:0 10px 0 15px;background:#ea8a34;display:flex;align-items:center;justify-content:center}
</style>
</head>
<body>

<section class="tile-board">

  <article class="quote-tile tile-teal">
    <svg class="tile-shape" viewBox="0 0 260 139" preserveAspectRatio="none">
      <path d="M174 0 C205 18 225 55 240 84 L260 73 L260 0 Z" fill="var(--teal)"/>
      <path d="M0 82 C50 100 95 112 135 108 C180 104 225 90 260 62 L260 139 L0 139 Z" fill="#e3f3f3"/>
    </svg>
    <div class="title-pill pill-navy">CONTRACT HIRE</div>
    <div class="price">£249.27<small>PLUS VAT</small></div>
    <p class="terms" style="top:51px">3 years,9+35,6k miles annually</p>
    <p class="includes" style="top:70px">Complete Servicing and Maintenance included</p>
    <div class="contact-btn btn-orange" style="left:9px;top:108px">
      <span class="btn-icon"><svg width="9" height="9" viewBox="0 0 24 24"><path fill="var(--orange)" d="M6.6 10.8a15 15 0 006.6 6.6l2.2-2.2c.3-.3.7-.4 1-.2 1.1.4 2.3.6 3.6.6.6 0 1 .4 1 1V20c0 .6-.4 1-1 1A17 17 0 013 4c0-.6.4-1 1-1h3.5c.6 0 1 .4 1 1 0 1.3.2 2.5.6 3.6.1.3 0 .7-.2 1z"/></svg></span>CONTACT US
    </div>
    <div class="chat-badge" style="left:225px;top:108px">Chatly</div>
  </article>

  <article class="quote-tile tile-gold">
    <svg class="tile-shape" viewBox="0 0 260 139" preserveAspectRatio="none">
      <defs><linearGradient id="goldFade" x1="0" y1="0" x2="1" y2="1"><stop offset="0" stop-color="var(--gold-soft)"/><stop offset="1" stop-color="var(--gold)"/></linearGradient></defs>
      <path d="M162 0 L260 0 L260 72 Z" fill="url(#goldFade)"/>
    </svg>
    <h2 class="headline"><span class="word-a">CONTRACT</span> <span class="word-b">HIRE</span></h2>
    <div class="price">£249.27<small>PLUS VAT</small></div>
    <p class="terms" style="top:51px">3 years,9+35,6k miles annually</p>
    <p class="includes" style="top:69px">Complete Servicing and Maintenance included</p>
    <div class="divider"></div>
    <div class="contact-btn btn-muted" style="left:23px;top:103px">
      <span class="btn-icon"><svg width="9" height="9" viewBox="0 0 24 24"><rect x="4" y="3" width="13" height="18" rx="1" fill="none" stroke="var(--orange-deep)" stroke-width="2"/><path d="M7 8h7M7 12h7M7 16h4" stroke="var(--orange-deep)" stroke-width="2"/></svg></span>CONTACT US
    </div>
    <div class="chat-badge" style="left:222px;top:103px">Chatly</div>
  </article>

  <article class="quote-tile tile-navy">
    <svg class="tile-shape" viewBox="0 0 260 139" preserveAspectRatio="none">
      <path d="M195 0 L260 0 L260 48 C245 52 225 52 210 42 C198 33 193 15 195 0 Z" fill="var(--navy)"/>
    </svg>
    <div class="title-pill pill-gold">Contract Hire</div>
    <div class="price">£<span class="amount-accent">249.27</span><small>PLUS VAT</small></div>
    <div class="icon-row">
      <svg viewBox="0 0 24 24"><rect x="3" y="5" width="18" height="16" rx="2" fill="none" stroke="var(--orange)" stroke-width="2.5"/><path d="M3 10h18M8 3v4M16 3v4" stroke="var(--orange)" stroke-width="2.5"/></svg>3 years
      <svg class="gap" viewBox="0 0 24 24"><circle cx="12" cy="8" r="4.5" fill="none" stroke="var(--orange)" stroke-width="2.5"/><path d="M3 22c0-5 4-8 9-8s9 3 9 8z" fill="none" stroke="var(--orange)" stroke-width="2.5"/></svg>9+35
      <svg class="gap" viewBox="0 0 24 24"><path d="M5 2h10l5 5v15H5z" fill="none" stroke="var(--orange)" stroke-width="2.5"/></svg>6k miles annually
    </div>
    <p class="includes" style="top:69px">Complete Servicing and Maintenance included</p>
    <div class="contact-btn btn-gradient" style="left:27px;top:101px">
      <span class="btn-icon"><svg width="12" height="12" viewBox="0 0 24 24"><rect x="4" y="3" width="13" height="18" rx="1" fill="none" stroke="#fff" stroke-width="2"/><path d="M7 8h7M7 12h7M7 16h4" stroke="#fff" stroke-width="2"/></svg></span>CONTACT US
    </div>
    <div class="chat-badge" style="left:225px;top:101px">Chatly</div>
  </article>

</section>

<section class="form-panel">
  <div class="hero-photo" role="img" aria-label="Photo of a smiling driver leaning out of a blue car window"></div>
  <form class="contact-form">
    <h2 class="form-title">Please Submit your Contact Details</h2>
    <div class="field field-name"><span class="field-icon"><svg width="8" height="8" viewBox="0 0 24 24"><circle cx="12" cy="7" r="5" fill="var(--navy)"/><path d="M3 23c0-6 4-9 9-9s9 3 9 9z" fill="var(--navy)"/></svg></span><span>Your Name</span></div>
    <div class="field field-email"><span class="field-icon"><svg width="8" height="8" viewBox="0 0 24 24"><rect x="2" y="5" width="20" height="14" rx="2" fill="var(--navy)"/><path d="M2 7l10 6 10-6" stroke="#fff" stroke-width="2" fill="none"/></svg></span><span>Email Address</span></div>
    <div class="field field-phone"><span class="field-icon"><svg width="8" height="8" viewBox="0 0 24 24"><path fill="var(--navy)" d="M6.6 10.8a15 15 0 006.6 6.6l2.2-2.2c.3-.3.7-.4 1-.2 1.1.4 2.3.6 3.6.6.6 0 1 .4 1 1V20c0 .6-.4 1-1 1A17 17 0 013 4c0-.6.4-1 1-1h3.5c.6 0 1 .4 1 1 0 1.3.2 2.5.6 3.6.1.3 0 .7-.2 1z"/></svg></span><span>Contact Number</span></div>
    <div class="field field-message"><span class="field-icon"><svg width="9" height="9" viewBox="0 0 24 24"><ellipse cx="10" cy="9" rx="8" ry="6" fill="var(--navy)"/><ellipse cx="16" cy="15" rx="7" ry="5" fill="var(--navy)" stroke="#fff" stroke-width="1.5"/></svg></span><span>Message</span></div>
    <div class="submit-btn">SUBMIT</div>
    <div class="close-btn"><svg width="9" height="9" viewBox="0 0 10 10"><path d="M1 1l8 8M9 1l-8 8" stroke="#fff" stroke-width="2.2"/></svg></div>
  </form>
</section>

</body>
</html>
```